Mens Jewellery Homepage - Modern, Stylish Mens Ring Brand - Homepage

Project Overview: KestrelHoops.com is a men's accessories brand specializing in high-quality mens rings.

The objective of this redesign is to create a modern, visually appealing homepage that is easy to navigate, showcases a wide range of rings, highlights personalization options, and builds trust with customers.

The new design should make a strong impression while reflecting the brand's premium quality and commitment to craftsmanship.

The focus will be on a sleek aesthetic that aligns with the tastes of men shopping for wedding bands, engagement rings, or fashion accessories.

Objectives:

Modern and Sleek Aesthetic:

A clean, minimalist design that emphasizes high-quality product imagery and thoughtful use of space.
Contemporary color palette that conveys elegance and sophistication, with accents that highlight key elements without overwhelming the user.

Consistent and easy-to-read typography that reflects the brand’s modern and masculine identity.

Showcasing Products:
Hero Section: A image to show off 3 or 4 ring designs that could be used for weddings or fashion.

Product Highlights: Below the hero banner, showcase product categories by color (see current website for colors)

Featured Products: Display a selection of “Top Rated” or “Customer Favorites” rings to help guide users toward popular choices.

Personalization Section:
A dedicated section promoting the ability to personalize rings, emphasizing features like engraving with names, dates, or special messages.
Include lifestyle images of personalized rings to inspire customers and give them an idea of what’s possible.
Use callouts such as “Make It Yours” or “Personalize Your Ring” to encourage users to explore the customization options available for each product.

Building Trust:

A space to show 5 or 6 testimonials and other trust elements

Symbols / text to show

free delivery
free returns
every ring stock
fast delivery
customer images (from reviews)

Driving Conversions:
Include a prominent call-to-action (CTA) button in the hero section with text like “Shop Now” or “Discover Our Collections.”

User Experience:
Fast, easy-to-navigate layout with simple and intuitive categories. Product categories and main sections should be clearly visible and easy to access without overwhelming the user.
Design the homepage to feel cohesive and uncluttered, with a logical flow from product discovery to personalization and checkout.

Visual Elements and Imagery:
Use ring images from our site, but add backgrounds etc to make the image on the homepage more interesting.

Personalization Options: Use visual representations (like ring mockups) showing where personalization options (such as engravings) would appear on the product.

I like (and would like to see some different designs from our current design)
Vorm.com for design
ridgeloops.com

Target Market(s)

Men - 20 to 35

Number of Pages Required

1 page

Requirements
Must have
• Easy navigation, Trust, Modern, Clean,
Nice to have
• Would like to see Different designs like Vorm.com - RidgeLoops.com

```html
<!DOCTYPE html>
<html lang="en">
<head>
<meta charset="utf-8">
<title>Kestrel Hoops — Men's Rings</title>
<link rel="stylesheet" href="https://fonts.googleapis.com/css2?family=Outfit:wght@400;500;600;700&family=Montserrat:wght@400;500;600&display=swap">
<style>
:root{
  --gold:#f9c344;
  --gold-soft:#fde7b0;
  --gold-pale:#fff4da;
  --ink:#111111;
  --text:#2b2b2b;
  --muted:#555555;
  --stone:#ece9e6;
  --line:#e4e1dd;
  --white:#ffffff;
}
*{box-sizing:border-box;margin:0;padding:0}
html,body{width:1200px;height:4175px;overflow:hidden}
body{position:relative;background:var(--white);font-family:"Montserrat",sans-serif;color:var(--text)}
.abs{position:absolute}
.heading{font-family:"Outfit",sans-serif;font-weight:500;color:var(--ink)}
.brand{display:flex;align-items:center;gap:12px;font-family:"Outfit",sans-serif;font-weight:600;letter-spacing:5px;font-size:17px;color:var(--ink)}
.brand-dot{width:52px;height:52px;border:4px solid var(--ink);border-radius:50%}
/* header */
.site-header{left:0;top:0;width:1200px;height:83px;display:flex;align-items:center;padding:0 141px;justify-content:space-between}
.main-nav{display:flex;gap:32px;font-family:"Outfit",sans-serif;font-weight:500;font-size:14px;color:var(--ink);margin-left:auto;margin-right:50px}
.main-nav span svg{margin-left:4px;vertical-align:middle}
.header-icons{display:flex;gap:12px}
.icon-btn{width:39px;height:39px;border-radius:50%;background:var(--gold);display:flex;align-items:center;justify-content:center}
/* hero */
.hero{left:0;top:83px;width:1200px;height:509px;display:flex}
.hero-photo-a{width:600px;height:100%;background:linear-gradient(135deg,#2f3a22 0%,#5c4632 45%,#a5703f 60%,#1f2325 100%)}
.hero-photo-b{width:600px;height:100%;background:linear-gradient(160deg,#6b4a2b 0%,#b27446 35%,#c19275 55%,#4a3a30 100%)}
.hero-copy{left:0;top:83px;width:1200px;height:509px;display:flex;flex-direction:column;align-items:center;padding-top:145px;color:var(--white);text-align:center}
.hero-copy h1{font-family:"Outfit",sans-serif;font-weight:700;font-size:50px;line-height:1.1;color:var(--white)}
.hero-copy p{font-family:"Outfit",sans-serif;font-size:18px;line-height:30px;margin-top:14px}
.btn{display:inline-flex;align-items:center;justify-content:center;gap:12px;border-radius:30px;font-family:"Outfit",sans-serif;font-weight:500;color:var(--ink)}
.btn-gold{background:var(--gold)}
.hero-copy .btn{margin-top:22px;width:198px;height:39px;font-size:14px;font-weight:600}
.arrow-dot{width:30px;height:30px;border-radius:50%;background:var(--ink);display:flex;align-items:center;justify-content:center}
/* section titles */
.section-title{left:0;width:1200px;text-align:center;font-size:31px}
.divider{left:0;width:1200px;display:flex;justify-content:center;align-items:center;gap:14px}
.divider i{display:block;width:52px;height:1px;background:var(--gold)}
.divider b{display:block;width:32px;height:24px;border-radius:12px;background:#cfcac4}
/* about */
.about-copy{left:141px;top:688px;width:440px}
.about-copy h2{font-size:28px}
.about-copy .divider{position:static;width:auto;justify-content:flex-start;margin-top:10px}
.about-copy .divider i{width:52px}
.about-copy p{font-size:13px;line-height:21px;margin-top:16px;color:var(--text)}
.pill-photo{border-radius:90px}
/* category */
.cat{width:200px;text-align:center}
.cat-visual{position:relative;width:178px;height:210px;margin:0 auto}
.cat-glow{position:absolute;left:0;bottom:0;width:178px;height:178px;border-radius:50%;background:linear-gradient(180deg,var(--white) 30%,var(--gold-soft) 80%,var(--gold) 100%)}
.cat-ring{position:absolute;left:24px;top:8px;width:130px;height:170px;border-radius:50%}
.cat-name{font-size:15px;margin-top:14px;color:var(--text)}
.cat-rule{width:20px;height:3px;background:var(--gold);margin:8px auto 0}
.btn-outline{width:148px;height:39px;border:1px solid var(--line);box-shadow:0 2px 6px rgba(0,0,0,.12);font-family:"Montserrat",sans-serif;font-size:14px;background:var(--white);margin-top:28px;justify-content:space-between;padding:0 4px 0 20px}
.btn-outline .arrow-dot{width:30px;height:30px}
/* featured */
.product{width:212px;text-align:center}
.product-photo{width:212px;height:211px;border-radius:14px;background:var(--stone);display:flex;align-items:center;justify-content:center}
.product-ring{width:130px;height:150px;border-radius:50%}
.product-name{font-size:13px;line-height:19px;margin-top:26px;color:var(--text)}
.slider-arrow{width:36px;height:36px;border-radius:50%;display:flex;align-items:center;justify-content:center}
/* banner */
.promo{left:141px;top:2496px;width:918px;height:342px;background:var(--stone);display:flex}
.promo-photo{width:321px;height:100%;background:linear-gradient(120deg,#2a2a2a 0%,#6e5d52 40%,#b7a79a 70%,#494441 100%)}
.promo-body{flex:1;display:flex;flex-direction:column;align-items:center;padding-top:46px;text-align:center}
.promo-body .divider{position:static;width:auto;margin-top:16px}
.promo-body .divider i{display:none}
.promo-body p{font-size:14px;line-height:22px;margin-top:14px;width:440px}
.promo-actions{display:flex;gap:38px;margin-top:28px}
.promo-actions .btn{height:40px;font-size:16px;padding:0 5px 0 24px;gap:14px}
/* testimonials */
.review{width:459px;height:211px;border:1px solid var(--line);border-radius:106px;display:flex;align-items:center;padding-left:26px;background:var(--white)}
.avatar{width:120px;height:120px;border-radius:50%;flex:none}
.review-body{margin-left:32px;width:270px}
.stars{color:var(--gold);font-size:12px;letter-spacing:4px}
.review-body p{font-size:12px;line-height:20px;margin-top:10px}
.review-body h4{font-weight:600;font-size:13px;margin-top:14px;color:var(--ink)}
.review-body span{font-size:13px;color:var(--muted)}
/* trust */
.footer-band{left:0;top:3709px;width:1200px;height:418px;background:var(--ink)}
.perk{width:212px;height:120px;border:2px solid var(--gold-soft);border-radius:10px;background:var(--white);display:flex;flex-direction:column;align-items:center}
.perk-icon{width:96px;height:96px;border-radius:50%;background:var(--ink);border:4px solid var(--white);margin-top:-50px}
.perk-label{margin-top:24px;background:var(--gold-pale);border-radius:20px;padding:8px 22px;font-family:"Outfit",sans-serif;font-weight:500;font-size:15px;color:var(--ink)}
/* footer */
.footer-col{color:var(--white)}
.footer-col h5{font-family:"Outfit",sans-serif;font-weight:500;font-size:17px}
.footer-about{left:141px;top:3889px;width:255px}
.footer-about .brand{color:var(--white)}
.footer-about .brand-dot{border-color:var(--white);width:50px;height:50px}
.footer-about p{font-size:11.5px;line-height:19px;margin-top:18px}
.quick-links{left:473px;top:3880px}
.quick-links ul{list-style:none;margin-top:20px}
.quick-links li{font-size:10px;line-height:27px}
.quick-links li::before{content:"•";margin-right:6px}
.contact{left:642px;top:3880px;width:240px}
.contact-item{display:flex;gap:10px;margin-top:18px;font-size:12px;line-height:16px}
.contact-item strong{font-weight:500}
.social{left:910px;top:3880px}
.social-item{display:flex;align-items:center;gap:12px;margin-top:12px;font-size:12.5px}
.social-item i{display:block;width:26px;height:26px;border:1.5px solid var(--white);border-radius:50%}
.social h5{margin-bottom:16px}
.copyright{left:0;top:4127px;width:1200px;height:48px;background:var(--gold);display:flex;align-items:center;justify-content:center;font-size:12px;color:var(--ink)}
</style>
</head>
<body>

<header class="site-header abs">
  <div class="brand"><span class="brand-dot"></span>KESTREL HOOPS</div>
  <nav class="main-nav">
    <span>Shop By Material<svg width="9" height="6" viewBox="0 0 9 6"><path d="M1 1l3.5 3.5L8 1" fill="none" stroke="#111" stroke-width="1.5"/></svg></span>
    <span>Shop By Color<svg width="9" height="6" viewBox="0 0 9 6"><path d="M1 1l3.5 3.5L8 1" fill="none" stroke="#111" stroke-width="1.5"/></svg></span>
    <span>Try At Home</span>
  </nav>
  <div class="header-icons">
    <span class="icon-btn"><svg width="18" height="18" viewBox="0 0 18 18"><circle cx="7.5" cy="7.5" r="5.5" fill="none" stroke="#111" stroke-width="1.8"/><path d="M11.5 11.5L16 16" stroke="#111" stroke-width="1.8"/></svg></span>
    <span class="icon-btn"><svg width="16" height="18" viewBox="0 0 16 18"><rect x="2" y="5" width="12" height="11" rx="2" fill="none" stroke="#111" stroke-width="1.6"/><path d="M5 7V4a3 3 0 016 0v3" fill="none" stroke="#111" stroke-width="1.6"/></svg></span>
  </div>
</header>

<section class="hero abs">
  <div class="hero-photo-a" role="img" aria-label="Rose gold lattice ring resting on a dark stone"></div>
  <div class="hero-photo-b" role="img" aria-label="Man's hand wearing a grey tungsten ring against a knitted sweater"></div>
</section>
<div class="hero-copy abs">
  <h1>Elevate Your Style</h1>
  <p>Handcrafted Rings with Free Fast Delivery &amp;<br>Hassle Free Returns</p>
  <span class="btn btn-gold">Discover Our Collections</span>
</div>

<section class="about-copy abs">
  <h2 class="heading">About to Kestrel Hoops</h2>
  <div class="divider"><b></b><i></i></div>
  <p>Lorem ipsum dolor sit amet, consectetuer adipiscing elit, sed diarim nonummy nibh euismod tincidunt ut laoreet dolore.</p>
  <p>Lorem ipsum dolor sit amet, consectetuer adipiscing elit, sed diarim nonummy nibh euismod tincidunt ut laoreet dolore magna aliquam erat volutpat. Ut wisi enim ad minim veniam, quis nostrud exercierr tation ullamcorper suscipit lobortis nisl ut aliquip ex ea commodoer consequat. Duis autem vel eum iriure dolor in hendrerit in rulputate at vero eros et accumsan et iusto odio dignissim.</p>
</section>
<div class="pill-photo abs" style="left:647px;top:689px;width:175px;height:300px;background:linear-gradient(160deg,#3a3a3a,#111 60%,#2a2a2a)" role="img" aria-label="Black branded ring gift box"></div>
<div class="pill-photo abs" style="left:848px;top:689px;width:211px;height:300px;background:linear-gradient(160deg,#d9c2a0,#b88e5e 50%,#8a6a45)" role="img" aria-label="Two rings lying on a wooden table"></div>

<h2 class="heading section-title abs" style="top:1072px">Shop By Category</h2>
<div class="divider abs" style="top:1118px"><i></i><b></b><i></i></div>

<div class="abs" style="left:161px;top:1168px;display:flex;gap:29px">
  <div class="cat"><div class="cat-visual"><div class="cat-glow"></div><div class="cat-ring" role="img" aria-label="Gold tungsten ring" style="background:radial-gradient(ellipse at 40% 40%,#fff3b8,#e0ad2a 55%,#b07d14)"></div></div><div class="cat-name">Tungsten Rings</div><div class="cat-rule"></div><span class="btn btn-outline">Shop Now<span class="arrow-dot"><svg width="12" height="12" viewBox="0 0 12 12"><path d="M2 10L10 2M4 2h6v6" fill="none" stroke="#fff" stroke-width="1.5"/></svg></span></span></div>
  <div class="cat"><div class="cat-visual"><div class="cat-glow"></div><div class="cat-ring" role="img" aria-label="Brushed titanium ring" style="background:radial-gradient(ellipse at 40% 40%,#fafafa,#b9b9b9 55%,#7c7c7c)"></div></div><div class="cat-name">Titanium Rings</div><div class="cat-rule"></div><span class="btn btn-outline">Shop Now<span class="arrow-dot"><svg width="12" height="12" viewBox="0 0 12 12"><path d="M2 10L10 2M4 2h6v6" fill="none" stroke="#fff" stroke-width="1.5"/></svg></span></span></div>
  <div class="cat"><div class="cat-visual"><div class="cat-glow"></div><div class="cat-ring" role="img" aria-label="Meteorite inlay ring with blue stripe" style="background:radial-gradient(ellipse at 40% 40%,#e9eef5,#7ea4d4 50%,#6f747a)"></div></div><div class="cat-name">Meteorite Rings</div><div class="cat-rule"></div><span class="btn btn-outline">Shop Now<span class="arrow-dot"><svg width="12" height="12" viewBox="0 0 12 12"><path d="M2 10L10 2M4 2h6v6" fill="none" stroke="#fff" stroke-width="1.5"/></svg></span></span></div>
  <div class="cat"><div class="cat-visual"><div class="cat-glow"></div><div class="cat-ring" role="img" aria-label="Carbon fibre ring with blue accents" style="background:radial-gradient(ellipse at 40% 40%,#dfe6ea,#5f7b86 50%,#2f3336)"></div></div><div class="cat-name">Carbon Fibre Rings</div><div class="cat-rule"></div><span class="btn btn-outline">Shop Now<span class="arrow-dot"><svg width="12" height="12" viewBox="0 0 12 12"><path d="M2 10L10 2M4 2h6v6" fill="none" stroke="#fff" stroke-width="1.5"/></svg></span></span></div>
</div>

<div class="abs" style="left:161px;top:1557px;display:flex;gap:29px">
  <div class="cat"><div class="cat-visual"><div class="cat-glow"></div><div class="cat-ring" role="img" aria-label="Silver ring with white shell inlay" style="background:radial-gradient(ellipse at 40% 40%,#ffffff,#e9e3d6 50%,#8d8d8d)"></div></div><div class="cat-name">Shell Rings</div><div class="cat-rule"></div><span class="btn btn-outline">Shop Now<span class="arrow-dot"><svg width="12" height="12" viewBox="0 0 12 12"><path d="M2 10L10 2M4 2h6v6" fill="none" stroke="#fff" stroke-width="1.5"/></svg></span></span></div>
  <div class="cat"><div class="cat-visual"><div class="cat-glow"></div><div class="cat-ring" role="img" aria-label="Black ceramic ring" style="background:radial-gradient(ellipse at 40% 40%,#6a6a6a,#1a1a1a 55%,#050505)"></div></div><div class="cat-name">Ceramic Rings</div><div class="cat-rule"></div><span class="btn btn-outline">Shop Now<span class="arrow-dot"><svg width="12" height="12" viewBox="0 0 12 12"><path d="M2 10L10 2M4 2h6v6" fill="none" stroke="#fff" stroke-width="1.5"/></svg></span></span></div>
  <div class="cat"><div class="cat-visual"><div class="cat-glow"></div><div class="cat-ring" role="img" aria-label="Silver ring with wood inlay" style="background:radial-gradient(ellipse at 40% 40%,#f2f2f2,#8a4a2a 50%,#7d7d7d)"></div></div><div class="cat-name">Wood Rings</div><div class="cat-rule"></div><span class="btn btn-outline">Shop Now<span class="arrow-dot"><svg width="12" height="12" viewBox="0 0 12 12"><path d="M2 10L10 2M4 2h6v6" fill="none" stroke="#fff" stroke-width="1.5"/></svg></span></span></div>
  <div class="cat"><div class="cat-visual"><div class="cat-glow"></div><div class="cat-ring" role="img" aria-label="Ring with antler inlay" style="background:radial-gradient(ellipse at 40% 40%,#ececec,#6b5a4b 50%,#444)"></div></div><div class="cat-name">Antler Rings</div><div class="cat-rule"></div><span class="btn btn-outline">Shop Now<span class="arrow-dot"><svg width="12" height="12" viewBox="0 0 12 12"><path d="M2 10L10 2M4 2h6v6" fill="none" stroke="#fff" stroke-width="1.5"/></svg></span></span></div>
</div>

<span class="btn btn-gold abs" style="left:496px;top:1914px;width:208px;height:42px;font-size:16px;padding-left:8px;gap:14px">View All Category<span class="arrow-dot"><svg width="12" height="12" viewBox="0 0 12 12"><path d="M2 10L10 2M4 2h6v6" fill="none" stroke="#fff" stroke-width="1.5"/></svg></span></span>

<h2 class="heading section-title abs" style="top:2034px">Featured Products</h2>
<div class="divider abs" style="top:2082px"><i></i><b></b><i></i></div>

<span class="slider-arrow abs" style="left:86px;top:2220px;border:1.5px solid var(--ink)"><svg width="14" height="12" viewBox="0 0 14 12"><path d="M13 6H2M6 1L1 6l5 5" fill="none" stroke="#111" stroke-width="2"/></svg></span>
<span class="slider-arrow abs" style="left:1078px;top:2220px;background:var(--gold)"><svg width="14" height="12" viewBox="0 0 14 12"><path d="M1 6h11M8 1l5 5-5 5" fill="none" stroke="#fff" stroke-width="2"/></svg></span>

<div class="abs" style="left:141px;top:2132px;display:flex;gap:24px">
  <div class="product"><div class="product-photo"><div class="product-ring" role="img" aria-label="Rose gold and black tungsten ring" style="background:radial-gradient(ellipse at 45% 45%,#e9e9e9,#c88a6e 50%,#222)"></div></div><div class="product-name">Veritas<br>Men's Tungsten Ring</div></div>
  <div class="product"><div class="product-photo"><div class="product-ring" role="img" aria-label="Black tungsten ring with wood stripe" style="background:radial-gradient(ellipse at 45% 45%,#555,#7a3f22 50%,#111)"></div></div><div class="product-name">Stag<br>Men's Tungsten Ring</div></div>
  <div class="product"><div class="product-photo"><div class="product-ring" role="img" aria-label="Black titanium ring" style="background:radial-gradient(ellipse at 45% 45%,#4a4a4a,#151515 55%,#000)"></div></div><div class="product-name">The Keen<br>Men's Titanium Ring</div></div>
  <div class="product"><div class="product-photo"><div class="product-ring" role="img" aria-label="Blue and silver titanium ring" style="background:radial-gradient(ellipse at 45% 45%,#e6e6e6,#1f4fa8 50%,#9a9a9a)"></div></div><div class="product-name">Calmer<br>Men's Titanium Ring</div></div>
</div>

<section class="promo abs">
  <div class="promo-photo" role="img" aria-label="Man's hand in pocket wearing a dark ring"></div>
  <div class="promo-body">
    <div class="brand"><span class="brand-dot"></span>KESTREL HOOPS</div>
    <div class="divider"><i></i><b></b><i></i></div>
    <p>Lorem ipsum dolor sit amet, consectetuer adipiscing elit sed diarim nonummy nibh euismod tincidunt ut laoreet</p>
    <div class="promo-actions">
      <span class="btn btn-gold">Shop Now<span class="arrow-dot"><svg width="12" height="12" viewBox="0 0 12 12"><path d="M2 10L10 2M4 2h6v6" fill="none" stroke="#fff" stroke-width="1.5"/></svg></span></span>
      <span class="btn btn-gold">Make It Yours<span class="arrow-dot"><svg width="12" height="12" viewBox="0 0 12 12"><path d="M2 10L10 2M4 2h6v6" fill="none" stroke="#fff" stroke-width="1.5"/></svg></span></span>
    </div>
  </div>
</section>

<h2 class="heading section-title abs" style="top:2916px">Customer Testimonials</h2>
<div class="divider abs" style="top:2963px"><i></i><b></b><i></i></div>

<div class="review abs" style="left:141px;top:3027px"><div class="avatar" role="img" aria-label="Customer portrait" style="background:linear-gradient(160deg,#c9c4bd,#6c6560)"></div><div class="review-body"><div class="stars">★★★★★</div><p>Lorem ipsum dolor sit amet, consectetuer adipiscing elit, sedti rim nonum</p><h4>Dana R</h4><span>The Forge</span></div></div>
<div class="review abs" style="left:600px;top:3027px"><div class="avatar" role="img" aria-label="Customer portrait" style="background:linear-gradient(160deg,#3ec08d,#2a5a8c)"></div><div class="review-body"><div class="stars">★★★★★</div><p>Lorem ipsum dolor sit amet, consectetuer adipiscing elit, sedti rim nonum</p><h4>Dana R</h4><span>The Forge</span></div></div>
<div class="review abs" style="left:141px;top:3238px"><div class="avatar" role="img" aria-label="Customer portrait" style="background:linear-gradient(160deg,#f3efe9,#b98f72)"></div><div class="review-body"><div class="stars">★★★★★</div><p>Lorem ipsum dolor sit amet, consectetuer adipiscing elit, sedti rim nonum</p><h4>Lena P</h4><span>The Crown</span></div></div>
<div class="review abs" style="left:600px;top:3238px"><div class="avatar" role="img" aria-label="Customer portrait" style="background:linear-gradient(160deg,#3fb3d6,#c23a35)"></div><div class="review-body"><div class="stars">★★★★★</div><p>Lorem ipsum dolor sit amet, consectetuer adipiscing elit, sedti rim nonum</p><h4>Lena P</h4><span>The Crown</span></div></div>

<span class="btn btn-gold abs" style="left:535px;top:3486px;width:130px;height:40px;font-size:16px;padding-left:10px;gap:12px">View All<span class="arrow-dot"><svg width="12" height="12" viewBox="0 0 12 12"><path d="M2 10L10 2M4 2h6v6" fill="none" stroke="#fff" stroke-width="1.5"/></svg></span></span>

<div class="footer-band abs"></div>

<div class="abs" style="left:141px;top:3662px;display:flex;gap:23px">
  <div class="perk"><div class="perk-icon" role="img" aria-label="Delivery truck icon"></div><span class="perk-label">Free Fast Delivery</span></div>
  <div class="perk"><div class="perk-icon" role="img" aria-label="Gift return icon"></div><span class="perk-label">Easy Free Returns</span></div>
  <div class="perk"><div class="perk-icon" role="img" aria-label="Warehouse stock icon"></div><span class="perk-label">Every Ring Stock</span></div>
  <div class="perk"><div class="perk-icon" role="img" aria-label="Five star review icon"></div><span class="perk-label">5 Star Reviews</span></div>
</div>

<div class="footer-col footer-about abs">
  <div class="brand"><span class="brand-dot"></span>KESTREL HOOPS</div>
  <p>Lorem ipsum dolor sit amet, conse are no ctetuer adipiscing eliit, sereed diam nonu mmyis nibhav euismod tincidunt utiitie laoreet dolore magna aliquam eratraitor volutpat. Utsav is mo we are amazing gyiese wisi enim aard veniam.</p>
</div>
<div class="footer-col quick-links abs">
  <h5>Quick Links</h5>
  <ul><li>Home</li><li>About Us</li><li>Products</li><li>Shop By Color</li><li>Contact Us</li></ul>
</div>
<div class="footer-col contact abs">
  <h5>Contact Details</h5>
  <div class="contact-item"><svg width="12" height="16" viewBox="0 0 12 16"><path d="M6 15s5-5.5 5-9A5 5 0 001 6c0 3.5 5 9 5 9z" fill="#fff"/><circle cx="6" cy="6" r="2" fill="#111"/></svg><div><strong>Address</strong><br>22 Ash Lane Eastbrook<br>West Sussex RH9 4QT UK</div></div>
  <div class="contact-item"><svg width="13" height="13" viewBox="0 0 13 13"><path d="M3 1l2 3-1.5 1.5a7 7 0 004 4L9 8l3 2-1.5 2.5C6 12.5.5 7 .5 2.5z" fill="#fff"/></svg><div><strong>Phone</strong><br>01632 960418</div></div>
  <div class="contact-item"><svg width="14" height="11" viewBox="0 0 14 11"><rect x=".5" y=".5" width="13" height="10" fill="#fff"/><path d="M1 1l6 5 6-5" fill="none" stroke="#111"/></svg><div><strong>Email</strong><br>hello@kestrelhoops.com</div></div>
</div>
<div class="footer-col social abs">
  <h5>Follow Us</h5>
  <div class="social-item"><i></i>Friendbook</div>
  <div class="social-item"><i></i>Chirper</div>
  <div class="social-item"><i></i>ViewTube</div>
  <div class="social-item"><i></i>Snapgram</div>
</div>

<div class="copyright abs">Copyright © 2024 Kestrel Hoops &nbsp;|&nbsp; All Right Reserved &nbsp;|&nbsp; Terms of Service &nbsp;|&nbsp; Privacy Policy</div>

</body>
</html>
```